Need a vitamin/supplement label

Hi,
I need a vitamin label designing for a product that will be sold online.
The label needs to have the following information on the front:
1) B12
2) Methycobalamin
3) 1000mcg
4) 90 Lozenges
5) Sublingual
6) Dietary Supplement
7) Vegetarian
Numbers 1 and 2 need to standout the most because the product will only be sold online so visibility is key.
Use this design as an inspiration:
http://www.shopvelmara.com/Corvelle-Naturals-Methylcobalamin-5000mcg-Lozenges/dp/Q7742KXRTA/ref=sr_1_2?ie=UTF8&qid=1381433791&sr=8-2&keywords=b12
The label should come across as premium.
The brand name is 'Quarlen Nutra' and I haven't had a logo designed so there's some freedom when it comes to that. It needs to be simple and clean.
If you need any clarifications then let me know.
Online

```html
<!DOCTYPE html>
<html lang="en">
<head>
<meta charset="utf-8">
<title>Quarlen Nutra B-12 Label</title>
<link rel="stylesheet" href="https://fonts.googleapis.com/css2?family=Arimo:ital,wght@0,400;0,600;0,700;1,700&family=Tinos:wght@400&display=swap">
<style>
  :root {
    --page-bg: #e6e6e6;
    --label-deep: #5e0828;
    --label-main: #990f44;
    --label-light: #b8386a;
    --accent-pink: #d8105a;
    --band-white: #ffffff;
    --b12-ink: #8d1243;
    --text-white: #ffffff;
    --art-tone: #c9879f;
  }
  * { margin: 0; padding: 0; box-sizing: border-box; }
  html, body { width: 1200px; height: 960px; overflow: hidden; }
  body {
    background: radial-gradient(ellipse at center, #f4f4f4 0%, var(--page-bg) 75%);
    font-family: "Arimo", Arial, sans-serif;
    position: relative;
  }
  .label {
    position: absolute;
    left: 235px; top: 180px;
    width: 730px; height: 600px;
    background: linear-gradient(90deg, var(--label-main) 0%, var(--label-light) 22%, var(--label-main) 48%, var(--label-main) 70%, var(--label-deep) 100%);
    color: var(--text-white);
    overflow: hidden;
  }
  .label__rule-top {
    position: absolute; left: 0; right: 0; top: 10px;
    height: 2px; background: rgba(255,255,255,0.85);
  }
  .brand {
    position: absolute; left: 190px; top: 45px;
    display: flex; align-items: center; gap: 14px;
  }
  .brand__dot {
    width: 50px; height: 50px; border-radius: 50%;
    background: var(--text-white);
  }
  .brand__name {
    font-family: "Tinos", "Times New Roman", serif;
    font-size: 40px; font-weight: 400; color: var(--text-white);
    letter-spacing: 0.3px;
  }
  .tagline {
    position: absolute; left: 160px; top: 138px;
    font-style: italic; font-weight: 700; font-size: 22px; line-height: 30px;
    text-align: center; width: 300px;
  }
  .neuron-art {
    position: absolute; left: 440px; top: 100px;
    width: 150px; height: 270px;
    border-radius: 50% 50% 20% 20%;
    background: radial-gradient(ellipse at 50% 30%, rgba(201,135,159,0.55) 0%, rgba(201,135,159,0.15) 60%, rgba(201,135,159,0) 75%);
  }
  .compound-tab {
    position: absolute; left: 205px; top: 208px;
    width: 305px; height: 28px;
    background: var(--accent-pink);
    border-radius: 8px 8px 0 0;
    font-size: 22px; font-weight: 600; font-variant: small-caps;
    letter-spacing: 3px; text-align: center; line-height: 26px;
    text-transform: lowercase;
  }
  .compound-tab::first-letter { text-transform: uppercase; }
  .vitamin-band {
    position: absolute; left: 0; top: 236px;
    width: 510px; height: 155px;
    background: var(--band-white);
    border-radius: 0 20px 20px 0;
  }
  .vitamin-band::after {
    content: ""; position: absolute; right: 0; top: 0;
    width: 14px; height: 40px;
    background: var(--accent-pink);
    clip-path: polygon(0 0, 100% 0, 100% 100%);
  }
  .vitamin-name {
    position: absolute; left: 235px; top: 252px;
    font-weight: 700; font-size: 128px; line-height: 120px;
    color: var(--b12-ink); letter-spacing: -1px;
  }
  .features { list-style: none; position: absolute; top: 412px; left: 0; }
  .features__item {
    position: absolute; white-space: nowrap;
    font-size: 26px; font-weight: 600;
  }
  .features__item::before {
    content: ""; display: inline-block; width: 7px; height: 7px;
    background: var(--text-white); margin-right: 8px; vertical-align: middle;
  }
  .features__item--1 { left: 220px; top: 0; }
  .features__item--2 { left: 235px; top: 36px; }
  .features__item--3 { left: 255px; top: 73px; }
  .label__rule-bottom {
    position: absolute; left: 205px; top: 517px;
    width: 325px; height: 2px; background: rgba(255,255,255,0.9);
  }
  .dose-count {
    position: absolute; left: 220px; top: 533px;
    font-size: 20px; font-weight: 600; word-spacing: 2px;
  }
  .dose-count__sep { margin: 0 10px; }
</style>
</head>
<body>
  <main class="label">
    <div class="label__rule-top"></div>
    <div class="brand">
      <span class="brand__dot"></span>
      <span class="brand__name">Quarlen Nutra</span>
    </div>
    <p class="tagline">Supports Nerve Cells and Brain Tissue</p>
    <div class="neuron-art" role="img" aria-label="Faint illustration of a nerve cell with branching dendrites"></div>
    <div class="compound-tab">Methycobalamin</div>
    <div class="vitamin-band"></div>
    <h1 class="vitamin-name">B-12</h1>
    <ul class="features">
      <li class="features__item features__item--1">Sublingual</li>
      <li class="features__item features__item--2">Dietary Supplement</li>
      <li class="features__item features__item--3">Vegetarian</li>
    </ul>
    <div class="label__rule-bottom"></div>
    <p class="dose-count">1000mcg<span class="dose-count__sep">I</span>90 Lozenges</p>
  </main>
</body>
</html>
```